Employment Agency Website Design

We are working with an employment agency in California.

Some sites to use for content/competitors and inspiration:

https://www.pinecrestjobs.com/us/en
https://www.velmorusa.com
https://www.dravenworks.us
https://www.quillora.com/en
https://www.tomvalusa.com
https://www.fernstaffing.com

Thank you for taking the time to consider designing a website for us. We are web developers based in Stockton, CA, USA. Most of our projects go through the same process. Understanding this process may help you win a project with us. We custom-code all of our websites in-house. We don’t have any requirements as to what tools you use for your design, but we prefer Figma files. For any design that we label as four-stars, we send it to the client for review. The client picks the final design they want us to use. Once we complete this process, we will continue to show additional clients all the four-star sites and purchase them later. Your designs will have multiple chances to sell. For better chances of success, we ask that you follow these guidelines.

IMAGES:
If you use any images or icons in the design, we ask that you have a link to the asset so we can purchase the image/icon. Most of the designs we submit do not have the customer’s images on them unless they have some great images. Be creative; show us the feeling you are trying to portray with your image choices. Use any royalty-free site you choose. We subscribe to Adobe and mainly use their images, but we can purchase images outside of Adobe. PLEASE NOTE: we will not submit designs to clients with watermarks on the images.

FONTS:
We ask that you identify the fonts used in the design. This can be done in a message if you want. We typically use Google Fonts and Adobe Fonts.

CONTENT:
We're always open to different content and ideas. We often submit designs with stock images so the client can see our vision. We typically take pictures after the website launch to use their images with our vision. Lorem Ipsum is fine for paragraphs, but we ask that you write the headers in correct English. We want to be able to show the vision and identify the sections of the website.

INSPIRATION:
We typically add a couple of links in the brief of websites we like to help you get started in your design.

REVISIONS:
We do not often ask for revisions of the designs unless we see something in the design that may not appeal to the client. If there are slight changes that we want to make, we do that in the development process.

FEEDBACK:
We rarely give feedback on designs during the design process. We are working on many website projects and do not have the time to provide feedback. We usually respond if your request is well thought out and asks specific questions, but a note asking “feedback, please” usually goes unanswered.

```html
<!DOCTYPE html>
<html lang="en">
<head>
<meta charset="utf-8">
<title>Northlane Talent — The Future of Work</title>
<link rel="stylesheet" href="https://fonts.googleapis.com/css2?family=Poppins:wght@400;500;600;700&display=swap">
<style>
:root{
  --red:#c1202f;
  --red-dark:#7a0f17;
  --ink:#1c1c1c;
  --white:#ffffff;
  --field:#e9e9f0;
  --grey-btn:#6d6d6d;
}
*{box-sizing:border-box;margin:0;padding:0}
html,body{width:1200px;height:3927px;overflow:hidden}
body{font-family:'Poppins',sans-serif;color:var(--ink);background:var(--white);position:relative}
.abs{position:absolute}

/* header */
.site-header{position:absolute;left:0;top:0;width:1200px;height:81px;background:var(--white)}
.brand{position:absolute;left:107px;top:24px;display:flex;align-items:center;gap:10px}
.brand-dot{width:28px;height:28px;border-radius:50%;background:var(--red)}
.brand-name{font-size:22px;font-weight:600;color:var(--ink);line-height:1;white-space:nowrap}
.main-nav{position:absolute;left:397px;top:29px;display:flex;gap:21px;font-size:16px;font-weight:600}
.header-tools{position:absolute;left:985px;top:27px;display:flex;align-items:center;gap:18px;font-size:16px;font-weight:600}

/* hero */
.hero{position:absolute;left:0;top:81px;width:1200px;height:652px;
  background:linear-gradient(100deg,#4e4a47 0%,#66605b 45%,#8b7065 70%,#a65a4f 88%,#b9443f 100%)}
.hero-eyebrow{position:absolute;left:100px;top:265px;display:flex;align-items:center;gap:26px;font-size:22px;font-weight:500;color:var(--white);letter-spacing:.2px;white-space:nowrap}
.hero-rule{display:block;width:172px;height:2px;background:var(--white)}
.hero-title{position:absolute;left:100px;top:307px;font-size:62px;font-weight:700;line-height:90px;color:var(--white)}
.btn{position:absolute;display:flex;align-items:center;justify-content:center;font-size:15px;font-weight:700;color:var(--white);text-transform:uppercase;border-radius:4px}
.btn-solid{background:var(--red)}
.btn-outline{border:3px solid var(--white)}

/* search */
.photo{position:absolute}
.section-title{font-size:48px;font-weight:600;color:var(--red);line-height:1.2}
.search-title{position:absolute;left:540px;top:845px}
.search-lead{position:absolute;left:540px;top:915px;width:530px;font-size:20px;line-height:31px}
.field{position:absolute;left:540px;width:560px;height:52px;background:var(--field);border-radius:4px;font-size:17px;color:#555;padding-left:20px;display:flex;align-items:center}
.search-btn{left:540px;top:1148px;width:560px;height:45px}

/* feature bands */
.band{position:absolute;background:var(--red);color:var(--white)}
.band h2{font-size:48px;font-weight:600;line-height:1.2;white-space:nowrap}
.band p{font-size:20.5px;line-height:30px;margin-top:16px}

/* career cards */
.career-title{position:absolute;left:100px;top:2347px}
.career-lead{position:absolute;left:100px;top:2419px;font-size:20.5px}
.card{position:absolute;width:322px;height:366px;border-radius:3px;overflow:hidden}
.card span{position:absolute;left:17px;bottom:20px;font-size:30px;font-weight:700;line-height:45px;color:var(--white)}

/* newsletter */
.newsletter{position:absolute;left:0;top:3323px;width:1200px;height:267px;background:var(--red);color:var(--white);text-align:center}
.newsletter h2{position:absolute;left:0;width:1200px;top:42px;font-size:48px;font-weight:600}
.newsletter p{position:absolute;left:0;width:1200px;top:117px;font-size:20.5px}
.email{position:absolute;left:311px;top:155px;width:476px;height:45px;background:var(--white);color:#999;font-size:17px;text-align:left;padding-left:20px;display:flex;align-items:center;border-radius:3px 0 0 3px}
.subscribe{position:absolute;left:787px;top:155px;width:101px;height:45px;background:var(--grey-btn);font-size:13px;font-weight:600;display:flex;align-items:center;justify-content:center;border-radius:0 3px 3px 0}

/* footer */
.site-footer{position:absolute;left:0;top:3590px;width:1200px;height:337px;background:var(--red-dark);color:var(--white)}
.footer-brand{position:absolute;left:100px;top:150px;display:flex;align-items:center;gap:12px}
.footer-brand .brand-dot{width:36px;height:36px;background:var(--white)}
.footer-brand .brand-name{color:var(--white);font-size:30px}
.footer-links{position:absolute;top:100px;list-style:none;font-size:16px;font-weight:600}
.footer-links li{height:41.5px}
.social-title{position:absolute;left:894px;top:100px;font-size:20px;font-weight:600}
.social{position:absolute;top:142px;left:863px;display:flex;gap:22px}
.social i{display:block;width:32px;height:32px;background:var(--white);border-radius:4px}
</style>
</head>
<body>

<header class="site-header">
  <div class="brand">
    <div class="brand-dot"></div>
    <div class="brand-name">Northlane Talent</div>
  </div>
  <nav class="main-nav">
    <span>Find Job</span><span>Hire Talent</span><span>Insights</span><span>Location</span><span>About Us</span>
  </nav>
  <div class="header-tools">
    <svg width="22" height="22" viewBox="0 0 22 22" fill="none" stroke="#1c1c1c" stroke-width="2.2"><circle cx="9" cy="9" r="7"/><line x1="14" y1="14" x2="20" y2="20"/></svg>
    <span>Sign Up</span>
  </div>
</header>

<section class="hero" role="img" aria-label="Smiling professional woman standing in a bright modern office">
</section>
<div class="hero-eyebrow">WELCOME TO NORTHLANE TALENT<span class="hero-rule"></span></div>
<h1 class="hero-title">The Future of<br>Work</h1>
<div class="btn btn-solid" style="left:100px;top:515px;width:237px;height:46px">Find a Job</div>
<div class="btn btn-outline" style="left:358px;top:515px;width:235px;height:46px">Find Talent</div>

<section>
  <div class="photo" role="img" aria-label="Man with laptop and coffee giving a thumbs up beside a plant wall"
       style="left:100px;top:834px;width:406px;height:366px;border-radius:3px;background:linear-gradient(135deg,#3f4b2c 0%,#6a6a3a 40%,#9a6a3c 75%,#c9a477 100%)"></div>
  <h2 class="section-title search-title">Open Job Positions</h2>
  <p class="search-lead">Browse our hand-curated job opportunities to find a job here to launch your career.</p>
  <div class="field" style="top:1000px">Job Type</div>
  <div class="field" style="top:1074px">Category
    <svg style="position:absolute;right:20px;top:20px" width="20" height="12" viewBox="0 0 20 12"><polygon points="0,0 20,0 10,11" fill="#1c1c1c"/></svg>
  </div>
  <div class="btn btn-solid search-btn abs">Search</div>
</section>

<section class="band" style="left:0;top:1308px;width:608px;height:467px">
  <div style="position:absolute;left:100px;top:75px;width:470px">
    <h2>Open Job Positions</h2>
    <p>Lorem ipsum dolor sit amet consectetur. Amet morbi lectus eleifend vestibulum euismod convallis nisl duis. Elit senectus velit mattis nulla sem sit. At sit pretium vulputate tortor massa diam ac. Semper pretium cursus eu morbi imperdiet.</p>
  </div>
  <div class="btn btn-outline" style="left:100px;top:354px;width:236px;height:46px">Find Employers</div>
</section>
<div class="photo" role="img" aria-label="Two women talking at a white table by a large window"
     style="left:608px;top:1308px;width:592px;height:467px;background:linear-gradient(120deg,#b9b6ae 0%,#d8d2c6 40%,#6f6a66 70%,#2d3444 100%)"></div>

<div class="photo" role="img" aria-label="Two women in a job interview at a table near city windows"
     style="left:0;top:1775px;width:592px;height:467px;background:linear-gradient(120deg,#d9d6cf 0%,#c9c3b6 45%,#6d6a64 75%,#2f3a4a 100%)"></div>
<section class="band" style="left:592px;top:1775px;width:608px;height:467px">
  <div style="position:absolute;left:47px;top:72px;width:470px">
    <h2>Looking fo Talent?</h2>
    <p>Lorem ipsum dolor sit amet consectetur. Amet morbi lectus eleifend vestibulum euismod convallis nisl duis. Elit senectus velit mattis nulla sem sit. At sit pretium vulputate tortor massa diam ac. Semper pretium cursus eu morbi imperdiet.</p>
  </div>
  <div class="btn btn-outline" style="left:47px;top:354px;width:236px;height:46px">Find Talent</div>
</section>

<section>
  <h2 class="section-title career-title">Move Your Career Forward</h2>
  <p class="career-lead">Lorem ipsum dolor sit amet consectetur. Amet morbi lectus eleifend</p>

  <div class="card" style="left:100px;top:2473px;background:linear-gradient(160deg,#5a524c,#3b3532)" role="img" aria-label="Laughing woman seated by a stone wall"><span>Find a Job That<br>Fits You</span></div>
  <div class="card" style="left:439px;top:2473px;background:linear-gradient(160deg,#8a8583,#4a4039)" role="img" aria-label="Woman working on a laptop"><span>Build Your<br>Resume</span></div>
  <div class="card" style="left:778px;top:2473px;background:linear-gradient(160deg,#4c5350,#2a2f3b)" role="img" aria-label="Man in a suit working at a desk"><span>Today's In-<br>Demand Job</span></div>

  <div class="card" style="left:100px;top:2856px;background:linear-gradient(160deg,#c9c9cb,#8d6b63)" role="img" aria-label="Excited woman celebrating"><span>Get Paid What<br>You're Worth</span></div>
  <div class="card" style="left:439px;top:2856px;background:linear-gradient(160deg,#8c5a48,#4d6f7a)" role="img" aria-label="Woman at a laptop against a brick wall"><span>Explore Job<br>Possibilities</span></div>
  <div class="card" style="left:778px;top:2856px;background:linear-gradient(160deg,#3b342d,#7a5c4e)" role="img" aria-label="Smiling woman in a cafe"><span>Join Northlane<br>Talent</span></div>
</section>

<section class="newsletter">
  <h2>Join Our News Letter</h2>
  <p>Subscribe to job alerts.</p>
  <div class="email">E-mail</div>
  <div class="subscribe">Subscribe</div>
</section>

<footer class="site-footer">
  <div class="footer-brand">
    <div class="brand-dot"></div>
    <div class="brand-name">Northlane Talent</div>
  </div>
  <ul class="footer-links" style="left:473px">
    <li>Privacy Policy</li><li>Terms of Service</li><li>Goverment Notice</li><li>Legal</li>
  </ul>
  <ul class="footer-links" style="left:703px">
    <li>Find Job</li><li>Hire Talent</li><li>Insights</li><li>Location</li><li>About Us</li>
  </ul>
  <div class="social-title">Social Media</div>
  <div class="social" aria-label="Social media links"><i></i><i></i><i></i><i></i></div>
</footer>

</body>
</html>
```